Quillmont Climate Business Card Design

Design new, 2 sides, business cards for a residential and light commercial heating, air conditioning contractor.

Target Market(s)

Homeowners, small businesses

Industry/Entity Type

Business

Contact Information for Business Card

Dominic Westerhall
Phone - 862-415-2736
Email
Address - PO box 518
Brightwater NJ 07912
Website - www.HarborBreezeLLC.example

Requirements
Must have
• logo, company colors, standard size with no die cut, so I can use nova stamp

```html
<!DOCTYPE html>
<html lang="en">
<head>
<meta charset="utf-8">
<title>Quillmont Climate Business Card</title>
<link rel="stylesheet" href="https://fonts.googleapis.com/css2?family=Roboto:wght@400;500;700&family=Playfair+Display:wght@700&display=swap">
<style>
  :root {
    --backdrop: #e4e4e4;
    --brick: #7a2327;
    --maroon: #6b1c2a;
    --gold: #e3b514;
    --orange: #e1861c;
    --flame: #d0311f;
    --cream: #f7e6b6;
    --paper: #f6f6f4;
    --ink: #3b1418;
  }
  * { box-sizing: border-box; margin: 0; padding: 0; }
  html, body { width: 1200px; height: 576px; overflow: hidden; }
  body {
    background: var(--backdrop);
    font-family: "Roboto", Arial, sans-serif;
    position: relative;
  }
  .card {
    position: absolute;
    top: 138px;
    width: 484px;
    height: 294px;
    overflow: hidden;
    box-shadow: 2px 3px 5px rgba(0,0,0,0.25);
  }
  .card--front { left: 81px; background: var(--brick); }
  .card--back { left: 602px; width: 482px; background: var(--paper); }

  .brand-name {
    position: absolute;
    font-family: "Roboto", Arial, sans-serif;
    font-weight: 700;
    text-align: center;
    line-height: 1.05;
  }
  .card--front .brand-name {
    left: 0; right: 0; top: 106px;
    font-size: 42px;
    color: var(--cream);
  }
  .card--back .brand-name {
    left: 274px; width: 180px; top: 52px;
    font-size: 30px;
    color: var(--maroon);
  }

  .service-band {
    position: absolute;
    left: 0; right: 0; top: 249px; height: 22px;
    background: var(--gold);
    color: var(--ink);
    font-size: 12.5px;
    line-height: 22px;
    text-align: center;
  }

  .holder {
    position: absolute;
    left: 24px; top: 28px;
  }
  .holder-name {
    font-family: "Playfair Display", Georgia, serif;
    font-size: 22px;
    font-weight: 700;
    color: var(--maroon);
    line-height: 1.2;
  }
  .holder-role {
    font-size: 11px;
    color: var(--ink);
    margin-top: 5px;
  }

  .contact-list {
    position: absolute;
    left: 30px; top: 160px;
    list-style: none;
  }
  .contact-list li {
    display: flex;
    align-items: center;
    height: 17.4px;
    font-size: 12.5px;
    color: var(--ink);
  }
  .contact-list svg { width: 11px; height: 11px; margin-right: 7px; fill: var(--flame); flex: none; }

  .waves { position: absolute; left: 0; top: 0; }

  .service-list {
    position: absolute;
    right: 12px; top: 214px;
    list-style: none;
    text-align: right;
    color: var(--maroon);
    font-size: 12px;
    font-weight: 500;
    line-height: 16px;
  }
  .service-list li { position: relative; padding-right: 18px; }
  .service-list .lead::after { content: "\00AB"; position: absolute; right: 0; top: 0; }
</style>
</head>
<body>

<section class="card card--front" aria-label="Card front">
  <div class="brand-name">Quillmont Climate</div>
  <div class="service-band">Residential &amp; Light Commercial Heating &nbsp;• Air Conditioning Contractor</div>
</section>

<section class="card card--back" aria-label="Card back">
  <svg class="waves" width="482" height="294" viewBox="0 0 482 294" aria-hidden="true">
    <path d="M0 278 C120 300 280 250 482 176 V294 H0 Z" fill="var(--orange)"/>
    <path d="M0 270 C120 296 280 244 482 172 L482 168 C300 230 130 282 0 266 Z" fill="#ffffff"/>
    <path d="M54 258 C190 272 320 220 482 160 L482 170 C330 226 190 272 54 258 Z" fill="var(--flame)"/>
    <path d="M0 238 C90 252 190 258 270 250 C190 276 90 280 0 272 Z" fill="var(--maroon)"/>
  </svg>

  <div class="holder">
    <h1 class="holder-name">Dominic Westerhall</h1>
    <p class="holder-role">Managing Director</p>
  </div>

  <div class="brand-name">Quillmont<br>Climate</div>

  <ul class="contact-list">
    <li><svg viewBox="0 0 12 12"><path d="M1 4 Q6 0 11 4 L9 5 L8 4 L4 4 L3 5 Z M3 6 H9 L10 11 H2 Z"/></svg>862-415-2736</li>
    <li><svg viewBox="0 0 12 12"><path d="M0 2 H12 V10 H0 Z"/><path d="M0 2 L6 7 L12 2" stroke="#fff" stroke-width="1.2" fill="none"/></svg>info@QuillmontClimateLLC.example</li>
    <li><svg viewBox="0 0 12 12"><path d="M6 0 C3 0 1.5 2 1.5 4.3 C1.5 7 6 12 6 12 C6 12 10.5 7 10.5 4.3 C10.5 2 9 0 6 0 Z"/><circle cx="6" cy="4.3" r="1.6" fill="#fff"/></svg>PO box 518 Brightwater NJ 07912</li>
    <li><svg viewBox="0 0 12 12"><circle cx="6" cy="6" r="5.5"/><path d="M0.5 6 H11.5 M6 0.5 V11.5" stroke="#fff" stroke-width="0.9"/></svg>QuillmontClimateLLC.example</li>
  </ul>

  <ul class="service-list">
    <li class="lead">Air Conditioning</li>
    <li>Contractor</li>
    <li class="lead">Residential and Light</li>
    <li>Commercial Heating</li>
  </ul>
</section>

</body>
</html>
```